Der Flyer soll das Format DIN 105 lang haben und später bei druckfalter.de gedruckt werden. Entsprechende Vorlagen sind bei druckfalter.de vorhanden. Der Flyer wird in der Mitte 1x gefalzt und beidseitige bedruckt. (Es gibt also eine Außenseite, eine Doppel Innenseiten und eine Rückseite)
Der Flyer soll Neupatienten sowie BEstandspatienten ansprechen und über die Ärzte und die Leistungen informieren. Siehe www.praxis-lindenhof-beispiel.de
Die Fotos auf der Homepage können verwendet werden, entsprechende Lizenzen für die Nutzung liegen vor. An besseren Ideen bin ich natürlich auch interessiert :-)
Datenübergabe in Adobe Illustrator (.ai) oder Adobe InDesign (.indd)
Vielen Dank und beste Grüße

```html
<!DOCTYPE html>
<html lang="de">
<head>
<meta charset="utf-8">
<title>Praxis Lindenhof – Flyer</title>
<link href="https://fonts.googleapis.com/css2?family=Quicksand:wght@400;500;600;700&display=swap" rel="stylesheet">
<style>
  :root {
    --pink: #e2448c;
    --pink-soft: #f3b6d0;
    --ink: #1f2733;
    --text: #2b2f36;
    --paper: #ffffff;
    --stage: #cbc2b9;
    --grey-photo: #d9dadd;
  }
  * { box-sizing: border-box; margin: 0; padding: 0; }
  html, body { width: 1200px; height: 2400px; overflow: hidden; }
  body {
    background: var(--stage);
    font-family: "Quicksand", sans-serif;
    color: var(--text);
    position: relative;
  }
  .spread {
    position: absolute;
    left: 60px;
    width: 1080px;
    height: 1080px;
    background: var(--paper);
    overflow: hidden;
    box-shadow: 0 6px 24px rgba(0,0,0,.12);
  }
  .spread--inner { top: 60px; }
  .spread--outer { top: 1200px; }

  /* ---------- brand mark ---------- */
  .brand {
    position: absolute;
    display: flex;
    align-items: center;
    gap: 14px;
    color: var(--pink);
    font-weight: 600;
    letter-spacing: 1px;
    white-space: nowrap;
  }
  .brand__square {
    width: 22px; height: 22px;
    background: var(--pink);
    flex: none;
  }

  /* ---------- inner spread ---------- */
  .photo-strip {
    position: absolute; top: 0; left: 0;
    width: 1080px; height: 172px;
    display: flex;
  }
  .photo-strip__tile { flex: 1; height: 100%; }
  .tile--meter { background: linear-gradient(135deg, #c9c9cc, #8d8f96); }
  .tile--syringe { background: linear-gradient(135deg, #b9bcc2, #e4e6ea); }
  .tile--gut { background: linear-gradient(135deg, #f0e3e4, #e9a9b8); }
  .tile--tubes { background: linear-gradient(135deg, #f4c3d4, #e68fb1); }
  .tile--skin { background: linear-gradient(135deg, #f3d9cd, #d8a89a); }
  .tile--ultrasound { background: linear-gradient(135deg, #dfe3e8, #a9b1bb); }

  .stethoscope-photo {
    position: absolute; left: 0; top: 470px;
    width: 1080px; height: 430px;
    background:
      linear-gradient(180deg, #ffffff 0%, rgba(255,255,255,0) 35%),
      linear-gradient(90deg, #b5bcc6 0%, #e3e6ea 55%, #f1dbe3 100%);
  }

  .about {
    position: absolute; left: 69px; top: 200px; width: 400px;
  }
  .about__title {
    color: var(--pink);
    font-size: 20px;
    font-weight: 600;
    margin-bottom: 6px;
  }
  .about__text {
    font-size: 18px;
    line-height: 1.2;
    margin-bottom: 26px;
    font-weight: 500;
  }

  .services {
    position: absolute; right: 64px; top: 230px;
    text-align: right;
    list-style: none;
  }
  .services__heading {
    font-size: 27px;
    font-weight: 600;
    color: var(--ink);
    margin-bottom: 14px;
  }
  .services__item {
    color: var(--pink);
    font-size: 20px;
    font-weight: 600;
    line-height: 44px;
  }
  .spread--inner .brand { left: 190px; top: 960px; font-size: 44px; }

  /* ---------- outer spread ---------- */
  .panel { position: absolute; top: 0; width: 540px; height: 1080px; }
  .panel--back { left: 0; }
  .panel--front { left: 540px; }
  .panel .brand { top: 75px; font-size: 42px; }
  .panel--back .brand { left: 90px; }
  .panel--front .brand { left: 90px; }

  .contacts { position: absolute; left: 72px; top: 236px; width: 440px; }
  .contacts__title {
    color: var(--pink);
    font-size: 20px;
    font-weight: 600;
    margin-bottom: 4px;
  }
  .contacts__text {
    font-size: 18px;
    line-height: 1.2;
    font-weight: 500;
    margin-bottom: 28px;
  }

  .portrait {
    position: absolute; top: 770px; height: 310px; width: 240px;
  }
  .portrait--left { left: 40px; background: linear-gradient(180deg, #ffffff 0%, #4a3a34 45%, #1c1a1a 100%); }
  .portrait--right { left: 260px; background: linear-gradient(180deg, #ffffff 0%, #6b4d47 40%, #e0559a 100%); }
  .portrait__name {
    position: absolute; bottom: 14px; left: 20px;
    color: #fff; font-size: 24px; font-weight: 500;
  }

  .doctor-photo {
    position: absolute; left: 0; top: 189px;
    width: 540px; height: 753px;
    background: linear-gradient(160deg, #e6e8ec 0%, #c9cdd4 30%, #e87fb1 60%, #d8458a 100%);
  }
  .hours {
    position: absolute; left: 167px; top: 480px;
    width: 237px; height: 250px;
    background: rgba(226, 68, 140, .72);
    color: #fff;
    padding: 16px 18px;
    font-size: 16px;
    font-weight: 500;
  }
  .hours__title { margin-bottom: 8px; }
  .hours__table { border-collapse: collapse; }
  .hours__table td { vertical-align: top; line-height: 1.25; padding-bottom: 6px; }
  .hours__table td:first-child { width: 80px; }
  .hours__note { font-size: 14px; font-weight: 600; margin-top: 2px; }

  .practice {
    position: absolute; left: 0; top: 960px; width: 540px;
    text-align: center;
  }
  .practice__doctors { color: var(--pink); font-size: 26px; font-weight: 600; margin-bottom: 4px; }
  .practice__line { font-size: 17px; line-height: 1.22; font-weight: 500; }
</style>
</head>
<body>

<!-- Inner spread -->
<section class="spread spread--inner">
  <div class="photo-strip">
    <div class="photo-strip__tile tile--meter" role="img" aria-label="Foto: Blutzuckermessgerät in Händen"></div>
    <div class="photo-strip__tile tile--syringe" role="img" aria-label="Foto: Spritze und Impfstoff-Fläschchen"></div>
    <div class="photo-strip__tile tile--gut" role="img" aria-label="Foto: Darm-Illustration vor dem Bauch"></div>
    <div class="photo-strip__tile tile--tubes" role="img" aria-label="Foto: Blutröhrchen auf rosa Grund"></div>
    <div class="photo-strip__tile tile--skin" role="img" aria-label="Foto: Hautuntersuchung mit Dermatoskop"></div>
    <div class="photo-strip__tile tile--ultrasound" role="img" aria-label="Foto: Ultraschalluntersuchung"></div>
  </div>

  <div class="stethoscope-photo" role="img" aria-label="Foto: Stethoskop auf EKG-Ausdruck"></div>

  <div class="about">
    <h3 class="about__title">Wir sind Ansprechpartner</h3>
    <p class="about__text">Als Hausärzte sind wir in allen Gesundheits-<br>fragen Ihre erste Anlaufstelle</p>
    <h3 class="about__title">Wir sind Koordinator</h3>
    <p class="about__text">Wir behalten den Überblick und leiten Untersuchungen für Sie in die Weg.</p>
    <h3 class="about__title">Wir begleiten Sie</h3>
    <p class="about__text">Wir beraten Sie und unterstützen Sie dabei wieder gesund zu werden und zu bleiben.</p>
  </div>

  <ul class="services">
    <li class="services__heading">UNSERE LEISTUNGEN</li>
    <li class="services__item">Checkup und Checkup Plus</li>
    <li class="services__item">Ruhe-EKG/Belastungs-EKG</li>
    <li class="services__item">24h-Blutdruckmessung</li>
    <li class="services__item">Ultraschalluntersuchung</li>
    <li class="services__item">Lungenfunktionsuntersuchung</li>
    <li class="services__item">Hautkrebsscreening</li>
    <li class="services__item">Impfberatung/ReisemedizinCheckup</li>
    <li class="services__item">Checkup Plus</li>
  </ul>

  <div class="brand"><span class="brand__square"></span>PRAXIS LINDENHOF</div>
</section>

<!-- Outer spread -->
<section class="spread spread--outer">
  <div class="panel panel--back">
    <div class="brand"><span class="brand__square"></span>PRAXIS LINDENHOF</div>

    <div class="contacts">
      <h3 class="contacts__title">Ärztlicher Bereitschaftsdienst 0800 111 222</h3>
      <p class="contacts__text">Ärztehaus 1, Nebengebäude der Kreisklinik Nord<br>Klinikstraße 3<br>10115 Beispielstadt<br>Telefon: 0800 111 222</p>
      <h3 class="contacts__title">Apothekennotdienst:</h3>
      <p class="contacts__text">Telefon: 0800 / 00 11 22 3</p>
      <h3 class="contacts__title">Augenärztlicher Notdienst:</h3>
      <p class="contacts__text">Telefon: 0800 111 222</p>
      <h3 class="contacts__title">Giftnotruf Region Süd:</h3>
      <p class="contacts__text">Telefon: 0761 / 1 23 45</p>
      <h3 class="contacts__title">Notaufnahme:</h3>
      <p class="contacts__text">Kreisklinik Nord Notfallambulanz<br>Klinikstraße 3<br>10115 Beispielstadt<br>Telefon: 01234 / 56 - 0</p>
    </div>

    <div class="portrait portrait--left" role="img" aria-label="Porträtfoto der Ärztin Dr. Albrecht in Schwarz">
      <span class="portrait__name">Dr. Albrecht</span>
    </div>
    <div class="portrait portrait--right" role="img" aria-label="Porträtfoto der Ärztin Dr. Sommerfeld in pinkem Kasack">
      <span class="portrait__name">Dr. Sommerfeld</span>
    </div>
  </div>

  <div class="panel panel--front">
    <div class="brand"><span class="brand__square"></span>PRAXIS LINDENHOF</div>

    <div class="doctor-photo" role="img" aria-label="Foto: Ärztin in pinkem Kasack hält ein Stethoskop nach vorn">
      <div class="hours">
        <p class="hours__title">Sprechzeiten der Praxis</p>
        <table class="hours__table">
          <tr><td>Mo – Di</td><td>08:30 – 12:00<br>15:00 – 18:00</td></tr>
          <tr><td>Mi</td><td>08:30 – 12:00</td></tr>
          <tr><td>Do</td><td>08:30 – 12:00<br>15:00 – 18:00</td></tr>
          <tr><td>Fr</td><td>08:30 – 12:00</td></tr>
          <tr><td>Sa – So</td><td>Geschlossen</td></tr>
        </table>
        <p class="hours__note">Termine nach Vereinbarung</p>
      </div>
    </div>

    <div class="practice">
      <p class="practice__doctors">Dr. Albrecht - Dr. Sommerfeld</p>
      <p class="practice__line">Praxis Lindenhof</p>
      <p class="practice__line">Birkenallee 7, 10115 Beispielstadt</p>
      <p class="practice__line">Tel: 01234-567 89</p>
      <p class="practice__line">praxis-lindenhof-beispiel.de</p>
    </div>
  </div>
</section>

</body>
</html>
```